KRL Stationery Design Project

Dear Designers,
We need a new stationery design for company to match our new logo.
Designers should provide a design for the following:
1. Business Card: 3.5x2 Inches.
2. Letterhead: A4 size.
3. Envelops: 25x35.5 Cm.
You can keep the Arabic name at the bottom of the logo Or you can use the separate attached Arabic Name.
Please refer to the attached logo guide for design information.
Sample Business Card information:
Name: Tarek Sowan
Position: Operation Manager
Tel: +966 920007164 Ex. 500
Fax: +966 (3)8842617
Mob: +966 (5)00263817
email: tarek@krl-example.com.sa
URL: www.krl-example.com.sa
Address:
Nakheel Heights, Suite 718
Zayed bin Omar Str.
Khobar, 31847
Saudi Arabia
Updates
Dear All,
Please note, we had uploaded our logo along with Arabic writing in Adobe illustrator format (.ai).
Regards,
Karim
Dear All,
A sample data for the business card had been added as per your request.
Regards,
Karim

```html
<!DOCTYPE html>
<html lang="en">
<head>
<meta charset="utf-8">
<title>KRL Envelope</title>
<link rel="stylesheet" href="https://fonts.googleapis.com/css2?family=Open+Sans:wght@400;700&display=swap">
<style>
  :root {
    --backdrop: #d4e3ed;
    --navy: #0b2d52;
    --paper: #ffffff;
    --strip: #a9abae;
    --ink: #3f4348;
    --white: #ffffff;
  }
  * { margin: 0; padding: 0; box-sizing: border-box; }
  html, body {
    width: 1200px;
    height: 900px;
    overflow: hidden;
    background: var(--backdrop);
    font-family: "Open Sans", Arial, sans-serif;
  }
  .canvas { position: relative; width: 1200px; height: 900px; }

  .flap {
    position: absolute;
    left: 44px; top: 106px;
    width: 122px; height: 710px;
  }
  .flap-mark {
    position: absolute;
    left: 105px; top: 460px;
    transform: translate(-50%, -50%) rotate(90deg);
    color: var(--white);
    font-weight: 700;
    font-size: 26px;
    letter-spacing: 1px;
  }

  .envelope-front {
    position: absolute;
    left: 165px; top: 106px;
    width: 1003px; height: 710px;
    background: var(--paper);
  }
  .bottom-strip {
    position: absolute;
    left: 0; bottom: 0;
    width: 100%; height: 12px;
    background: var(--strip);
  }
  .brand-name {
    position: absolute;
    left: 44px; top: 30px;
    color: var(--navy);
    font-weight: 700;
    font-size: 46px;
    line-height: 1;
    letter-spacing: 1px;
  }

  .sender {
    position: absolute;
    left: 42px; top: 610px;
    color: var(--ink);
    font-size: 9px;
    line-height: 12px;
  }
  .sender-address { margin-bottom: 4px; }
  .contact-line { display: flex; align-items: center; gap: 5px; }
  .contact-icon { width: 10px; height: 10px; fill: var(--navy); }

  .web-tab {
    position: absolute;
    right: 48px; bottom: 0;
    width: 242px; height: 30px;
  }
  .web-tab svg { position: absolute; inset: 0; }
  .web-address {
    position: absolute;
    left: 0; right: 0; top: 5px;
    text-align: center;
    color: var(--white);
    font-size: 11px;
  }
</style>
</head>
<body>
<main class="canvas">

  <svg class="flap" viewBox="0 0 122 710" aria-hidden="true">
    <path d="M122 0 L122 710 L60 700 Q0 692 0 650 L0 72 Q0 30 55 22 Z" fill="var(--navy)"/>
  </svg>
  <div class="flap-mark">KRL</div>

  <section class="envelope-front">
    <div class="brand-name">KRL</div>

    <address class="sender">
      <p class="sender-address">Nakheel Heights, Suite 718<br>Zayed bin Omar Str.<br>Khobar, 31847, Saudi Arabia</p>
      <p class="contact-line">
        <svg class="contact-icon" viewBox="0 0 10 10" aria-hidden="true"><path d="M2 0.5 L4 2.5 L3 4 Q4.5 6 6 7 L7.5 6 L9.5 8 L8 9.5 Q3.5 9 0.5 2 Z"/></svg>
        +966 920007164 Ex. 500
      </p>
      <p class="contact-line">
        <svg class="contact-icon" viewBox="0 0 10 10" aria-hidden="true"><rect x="2.5" y="0.5" width="5" height="3"/><rect x="0.5" y="4" width="9" height="5.5" rx="1"/></svg>
        +966 (3)8842617
      </p>
      <p class="contact-line">
        <svg class="contact-icon" viewBox="0 0 10 10" aria-hidden="true"><path d="M0.5 2 H9.5 V8.5 H0.5 Z M0.5 2 L5 5.5 L9.5 2" fill="none" stroke="var(--navy)" stroke-width="1.2"/></svg>
        info@krl-example.com.sa
      </p>
    </address>

    <div class="web-tab">
      <svg viewBox="0 0 242 30" aria-hidden="true">
        <path d="M0 30 L10 6 Q13 0 20 0 L222 0 Q229 0 232 6 L242 30 Z" fill="var(--navy)"/>
      </svg>
      <span class="web-address">www.krl-example.com.sa</span>
    </div>

    <div class="bottom-strip"></div>
  </section>

</main>
</body>
</html>
```